Step and Repeat Backdrop for wedding reception photo booth

Would like to have a Step and Repeat Backdrop (8 foot high by 10 foot wide) that incorporates the wedding logo (attached) and the names Helen and Gavin. Background should be white, and wedding colors are burgundy and gold. Show me creativity :-) I have included some random samples.

```html
<!DOCTYPE html>
<html lang="en">
<head>
<meta charset="utf-8">
<title>Helen &amp; Gavin — Step and Repeat Backdrop</title>
<link rel="stylesheet" href="https://fonts.googleapis.com/css2?family=Playfair+Display:wght@600;700&display=swap">
<style>
  :root {
    --page-bg: #e9e9eb;
    --backdrop-white: #ffffff;
    --burgundy: #8e1537;
    --gold: #dc9b2a;
    --gold-deep: #c77a26;
    --gold-light: #f0bd33;
  }
  * { box-sizing: border-box; margin: 0; padding: 0; }
  html, body {
    width: 1200px;
    height: 1200px;
    overflow: hidden;
    background: var(--page-bg);
  }
  .canvas {
    position: relative;
    width: 1200px;
    height: 1200px;
  }
  .backdrop {
    position: absolute;
    left: 30px;
    top: 144px;
    width: 1140px;
    height: 912px;
    background: var(--backdrop-white);
    box-shadow: 0 2px 10px rgba(0, 0, 0, 0.08);
  }
  .repeat-grid {
    position: absolute;
    left: 2px;
    top: 22px;
    display: grid;
    grid-template-columns: repeat(8, 142px);
    grid-template-rows: repeat(8, 109px);
  }
  .monogram-tile {
    display: flex;
    align-items: center;
    justify-content: center;
    font-family: "Playfair Display", serif;
    font-weight: 700;
    font-size: 40px;
    letter-spacing: -2px;
    color: var(--burgundy);
    line-height: 1;
  }
  .monogram-tile--blank { visibility: hidden; }

  .feature-flourish {
    position: absolute;
    left: 440px;
    width: 260px;
    height: 56px;
    border-radius: 28px;
    background: linear-gradient(90deg, rgba(199,122,38,0.18), rgba(240,189,51,0.18));
  }
  .feature-flourish--top { top: 262px; }
  .feature-flourish--bottom { top: 480px; }

  .feature-monogram {
    position: absolute;
    left: 0;
    width: 1140px;
    top: 338px;
    text-align: center;
    font-family: "Playfair Display", serif;
    font-weight: 700;
    font-size: 120px;
    letter-spacing: -6px;
    color: var(--gold);
    line-height: 1;
  }
  .couple-names {
    position: absolute;
    left: 0;
    width: 1140px;
    top: 602px;
    display: flex;
    align-items: center;
    justify-content: center;
    gap: 24px;
    font-family: "Playfair Display", serif;
    font-weight: 600;
    font-size: 40px;
    color: var(--gold);
    line-height: 1;
  }
  .couple-names__name { letter-spacing: 20px; margin-right: -20px; }
  .couple-names__ring {
    width: 44px;
    height: 44px;
    border: 3px solid var(--gold);
    border-radius: 50%;
  }
</style>
</head>
<body>
<main class="canvas">
  <section class="backdrop" aria-label="Helen and Gavin step and repeat backdrop">
    <div class="repeat-grid">
      <span class="monogram-tile">H&amp;G</span><span class="monogram-tile">H&amp;G</span><span class="monogram-tile">H&amp;G</span><span class="monogram-tile">H&amp;G</span><span class="monogram-tile">H&amp;G</span><span class="monogram-tile">H&amp;G</span><span class="monogram-tile">H&amp;G</span><span class="monogram-tile">H&amp;G</span>
      <span class="monogram-tile">H&amp;G</span><span class="monogram-tile">H&amp;G</span><span class="monogram-tile">H&amp;G</span><span class="monogram-tile">H&amp;G</span><span class="monogram-tile">H&amp;G</span><span class="monogram-tile">H&amp;G</span><span class="monogram-tile">H&amp;G</span><span class="monogram-tile">H&amp;G</span>
      <span class="monogram-tile">H&amp;G</span><span class="monogram-tile">H&amp;G</span><span class="monogram-tile">H&amp;G</span><span class="monogram-tile monogram-tile--blank"></span><span class="monogram-tile monogram-tile--blank"></span><span class="monogram-tile">H&amp;G</span><span class="monogram-tile">H&amp;G</span><span class="monogram-tile">H&amp;G</span>
      <span class="monogram-tile">H&amp;G</span><span class="monogram-tile">H&amp;G</span><span class="monogram-tile">H&amp;G</span><span class="monogram-tile monogram-tile--blank"></span><span class="monogram-tile monogram-tile--blank"></span><span class="monogram-tile">H&amp;G</span><span class="monogram-tile">H&amp;G</span><span class="monogram-tile">H&amp;G</span>
      <span class="monogram-tile">H&amp;G</span><span class="monogram-tile">H&amp;G</span><span class="monogram-tile">H&amp;G</span><span class="monogram-tile monogram-tile--blank"></span><span class="monogram-tile monogram-tile--blank"></span><span class="monogram-tile">H&amp;G</span><span class="monogram-tile">H&amp;G</span><span class="monogram-tile">H&amp;G</span>
      <span class="monogram-tile">H&amp;G</span><span class="monogram-tile">H&amp;G</span><span class="monogram-tile monogram-tile--blank"></span><span class="monogram-tile monogram-tile--blank"></span><span class="monogram-tile monogram-tile--blank"></span><span class="monogram-tile monogram-tile--blank"></span><span class="monogram-tile">H&amp;G</span><span class="monogram-tile">H&amp;G</span>
      <span class="monogram-tile">H&amp;G</span><span class="monogram-tile">H&amp;G</span><span class="monogram-tile">H&amp;G</span><span class="monogram-tile">H&amp;G</span><span class="monogram-tile">H&amp;G</span><span class="monogram-tile">H&amp;G</span><span class="monogram-tile">H&amp;G</span><span class="monogram-tile">H&amp;G</span>
      <span class="monogram-tile">H&amp;G</span><span class="monogram-tile">H&amp;G</span><span class="monogram-tile">H&amp;G</span><span class="monogram-tile">H&amp;G</span><span class="monogram-tile">H&amp;G</span><span class="monogram-tile">H&amp;G</span><span class="monogram-tile">H&amp;G</span><span class="monogram-tile">H&amp;G</span>
    </div>

    <div class="feature-flourish feature-flourish--top" role="img" aria-label="Gold ornamental flourish above the monogram"></div>
    <div class="feature-monogram">H&amp;G</div>
    <div class="feature-flourish feature-flourish--bottom" role="img" aria-label="Gold ornamental flourish below the monogram"></div>

    <div class="couple-names">
      <span class="couple-names__name">Helen</span>
      <span class="couple-names__ring" aria-hidden="true"></span>
      <span class="couple-names__name">Gavin</span>
    </div>
  </section>
</main>
</body>
</html>
```